Exciting new website for concierge aesthetic company

Simple, elegant, fresh design for female owned concierge aesthetic company, catering to both men and women ages 30-60. We would like a home page with an exciting catch phrase, a brief description of the company and a section to fill out an appointment request that includes a section for a referral. Please also have a book appointment link in the header of all pages that will link back to booking information form on home page. Separate pages to include:
- Services = 3 different services. Each service stating the name of the service and then providing a brief description. 3 services are "Private Session" for 1 client, "Group Session" for 2-5 clients, "Party" for 6+ clients. Will provide service descriptions text later. Item at bottom of page to allow description of how to "Host a Party".
- Products = 4 different product lines. Will provide pictures of product, brief description and link to manufacturer's website.
- Stories = brief client reviews to include before and after photos
- About us = Personal picture with brief description of owner's fun, exciting and family focussed lifestyle.
*Our domain is registered with varnix and we be using varnix for website hosting.

Target Market(s)

30-60 year old men and women, but mostly women

Industry/Entity Type

beauty and aesthetics

Coding

Coded - Design and coding required

Number of Pages Required

5+ page

Font styles to use
Sans Serif
Script

Colors
59FF00
82FF00
B8FF75
E3FFCB
F4FFEA
FFC000
F8CF3A
FAE287
FDF2CF
FEFAEE
F0912C
F2A743
F7CA91
FBE8D2
FDF5EE
E54698
E96AAD
F1A4CE
F9D9EA
FCEFF6

Requirements
Must have
• coded for varnix
Should not have
• corny pictures. No needles in pictures or graphics. No medical office or medical chair in pictures.

```html
<!DOCTYPE html>
<html lang="en">
<head>
<meta charset="utf-8">
<title>Glow Muse — Concierge Aesthetics</title>
<link href="https://fonts.googleapis.com/css2?family=Mulish:wght@400;600;700;800&family=Great+Vibes&display=swap" rel="stylesheet">
<style>
:root{
  --pink:#e5177f;
  --pink-soft:#e54698;
  --orange:#ff8a00;
  --orange-deep:#f0912c;
  --ink:#111111;
  --text:#333333;
  --white:#ffffff;
  --black:#000000;
  --sans:'Mulish', Arial, sans-serif;
  --script:'Great Vibes', cursive;
}
*{margin:0;padding:0;box-sizing:border-box}
html,body{width:1200px;height:3492px;overflow:hidden;background:var(--white)}
body{font-family:var(--sans);color:var(--text);position:relative}
.page{position:relative;width:1200px;height:3492px;overflow:hidden}
.abs{position:absolute}
a{color:inherit;text-decoration:none}

/* top bar */
.topbar{left:0;top:0;width:1200px;height:50px;background:linear-gradient(90deg,var(--pink) 0%,#f2523f 55%,var(--orange) 100%);color:var(--white);font-size:15px}
.topbar .item{position:absolute;top:15px;display:flex;align-items:center;gap:8px}
.dots{position:absolute;right:116px;top:18px;display:flex;gap:9px}
.dots span{width:11px;height:11px;border-radius:50%;background:var(--white)}

/* nav */
.nav a{position:absolute;top:81px;font-size:16px;color:var(--ink)}
.nav a.active{color:var(--orange)}
.brand{left:490px;top:78px;width:220px;text-align:center;font-family:var(--sans);font-weight:800;font-size:30px;color:var(--pink)}
.phone{left:716px;top:72px;display:flex;align-items:center;gap:10px;font-size:18px;font-weight:700;color:var(--ink)}
.phone .ic{width:36px;height:36px;border-radius:50%;background:var(--pink);display:flex;align-items:center;justify-content:center}
.btn{display:inline-flex;align-items:center;justify-content:center;gap:10px;border-radius:40px;background:var(--orange);color:var(--white);font-weight:700}
.book{left:918px;top:67px;width:171px;height:40px;font-size:15px}

/* hero */
.hero-photo{left:0;top:110px;width:1200px;height:720px;background:linear-gradient(110deg,#e9e6e5 0%,#d8cfc9 45%,#e8d5c9 65%,#f1ece9 100%)}
.hero .welcome{left:111px;top:324px;font-size:22px;font-weight:700;color:var(--ink)}
.hero .name{left:108px;top:355px;font-family:var(--script);font-size:92px;color:var(--pink);line-height:1}
.hero p{left:111px;top:460px;width:400px;font-size:14px;line-height:26px;color:var(--ink)}
.start{left:111px;top:535px;width:153px;height:50px;font-size:16px}

/* sessions */
.session{border-radius:50%;border:6px solid var(--white);box-shadow:0 8px 24px rgba(0,0,0,.18);display:flex;flex-direction:column;align-items:center;justify-content:center;color:var(--white);font-weight:700;background:var(--orange)}
.session.small{width:296px;height:296px;font-size:22px}
.session.big{width:344px;height:344px;font-size:35px;background:linear-gradient(90deg,var(--pink) 0%,#f4504d 60%,var(--orange) 100%)}
.session svg{margin-bottom:14px}
.badge{border-radius:50%;background:var(--pink);color:var(--white);font-weight:700;font-size:14px;line-height:17px;text-align:center;display:flex;align-items:center;justify-content:center;border:3px solid var(--white)}
.badge.big{background:var(--orange);font-size:16px;line-height:19px}

/* section headings */
.kicker{font-family:var(--script);font-size:28px;color:var(--pink);width:100%;text-align:center}
.heading{font-size:40px;font-weight:700;color:var(--ink);width:100%;text-align:center;letter-spacing:.5px}

.about p{left:160px;top:1280px;width:880px;text-align:center;font-size:15px;line-height:26px;color:var(--ink)}
.learn{height:58px;width:180px;font-size:16px;letter-spacing:.3px}

/* products */
.products .kicker{color:var(--orange)}
.products .heading{color:var(--white)}
.card{width:228px;height:402px;background:var(--white);border-radius:114px;text-align:center;padding-top:190px}
.card .thumb{position:absolute;left:31px;top:0;width:166px;height:166px;border-radius:50%}
.card h3{font-size:19px;font-weight:600;color:var(--ink);line-height:27px;padding:0 4px}
.card p{font-size:15px;line-height:26px;color:var(--text);margin-top:8px;padding:0 12px}
.card a{display:inline-block;margin-top:4px;color:var(--orange);font-size:15px;font-weight:600;text-decoration:underline}
.arrow{width:32px;height:32px;border-radius:50%;display:flex;align-items:center;justify-content:center}

/* stories */
.before{left:111px;top:2414px;width:224px;height:352px;background:linear-gradient(160deg,#e7e2de,#cdbfb5 60%,#ece9e6);border-radius:4px}
.after{left:340px;top:2498px;width:224px;height:366px;background:linear-gradient(160deg,#ebe7e4,#d2c4b9 55%,#efedeb);border-radius:4px}
.tag{font-size:26px;font-weight:600}
.stories .kicker{text-align:left;width:auto}
.stories h2{left:605px;top:2460px;font-size:36px;font-weight:600;color:var(--ink)}
.stories p{left:605px;top:2514px;width:490px;font-size:15px;line-height:25.8px;color:var(--ink)}

/* footer */
.footer{color:var(--white)}
.footer .fbrand{left:127px;top:3058px;font-size:40px;font-weight:800;color:var(--orange);display:flex;align-items:center;gap:14px}
.footer .fbrand i{width:26px;height:26px;border-radius:50%;background:var(--pink);display:block}
.footer h4{font-size:17px;font-weight:700}
.footer ul{list-style:none;font-size:15px;line-height:30px}
.news{left:597px;top:3070px;font-size:31px;font-weight:600}
.email{left:595px;top:3140px;width:322px;border-bottom:1px solid #555;padding-bottom:12px;font-size:15px;color:#ddd}
.join{left:944px;top:3136px;width:142px;height:42px;font-size:15px}
.contact{left:595px;top:3212px;font-size:15px;font-weight:700;display:flex;gap:25px}
.fdots{left:970px;top:3216px;display:flex;gap:15px}
.fdots span{width:13px;height:13px;border-radius:50%;background:var(--pink)}
.rule{left:116px;top:3404px;width:976px;height:1px;background:#333}
.copy{left:0;top:3436px;width:1200px;text-align:center;font-size:15px}
</style>
</head>
<body>
<div class="page">

  <!-- hero photo area -->
  <div class="abs hero-photo" role="img" aria-label="Photo of a relaxed client receiving a gentle facial treatment from a professional"></div>

  <!-- white curve above hero -->
  <svg class="abs" style="left:0;top:40px" width="1200" height="140" viewBox="0 0 1200 140" aria-hidden="true">
    <path d="M0 0 H1200 V82 C1080 110 960 126 820 118 C700 110 600 128 470 126 C300 124 160 96 0 140 Z" fill="#fff"/>
  </svg>
  <!-- white curve below hero -->
  <svg class="abs" style="left:0;top:740px" width="1200" height="110" viewBox="0 0 1200 110" aria-hidden="true">
    <path d="M0 68 C150 40 300 30 460 46 C640 64 760 90 900 72 C1020 56 1120 28 1200 50 V110 H0 Z" fill="#fff"/>
  </svg>

  <!-- top bar -->
  <div class="abs topbar">
    <div class="item" style="left:111px">
      <svg width="15" height="12" viewBox="0 0 15 12"><rect x="0.5" y="0.5" width="14" height="11" rx="1.5" fill="#fff"/><path d="M1 1.5 L7.5 7 L14 1.5" stroke="#f05a4a" stroke-width="1.4" fill="none"/></svg>
      hello@glowmuse.co
    </div>
    <div class="item" style="left:310px">
      <svg width="11" height="15" viewBox="0 0 11 15"><path d="M5.5 0 C2.5 0 0 2.4 0 5.4 C0 9.4 5.5 15 5.5 15 C5.5 15 11 9.4 11 5.4 C11 2.4 8.5 0 5.5 0Z" fill="#fff"/><circle cx="5.5" cy="5.4" r="2" fill="#f35d3d"/></svg>
      A12 Lorem ipsum dolor sit amet
    </div>
    <div class="item" style="left:916px;font-size:14px">
      <svg width="13" height="12" viewBox="0 0 13 12"><path d="M0 4.5 H6 V1.5 L11 6 L6 10.5 V7.5 H0Z" fill="#fff"/></svg>
      Login
    </div>
    <div class="dots" aria-label="Social links"><span></span><span></span><span></span><span></span></div>
  </div>

  <!-- nav -->
  <nav class="nav">
    <a class="active" style="left:134px">Home</a>
    <a style="left:223px">About Us</a>
    <a style="left:334px">Stories</a>
    <a style="left:430px">Services</a>
  </nav>
  <div class="abs brand">Glow Muse</div>
  <div class="abs phone">
    <span class="ic"><svg width="16" height="16" viewBox="0 0 16 16"><path d="M3.5 1 L6 1.5 L7 5 L5.3 6.3 C6.2 8.3 7.7 9.8 9.7 10.7 L11 9 L14.5 10 L15 12.5 C15 14 14 15 12.5 15 C6.5 15 1 9.5 1 3.5 C1 2 2 1 3.5 1Z" fill="#fff"/></svg></span>
    +1 555 014 2290
  </div>
  <a class="abs btn book">Book Appointment</a>

  <!-- hero text -->
  <section class="hero">
    <div class="abs welcome">Welcome To</div>
    <div class="abs name">Glow Muse</div>
    <p class="abs">Lorem ipsum dolor sit amet, consectetur adipiscing elit, sed do eiusmod tempor incididunt ut labore et dolore</p>
    <a class="abs btn start">Get Started
      <svg width="14" height="14" viewBox="0 0 14 14"><circle cx="7" cy="7" r="7" fill="#fff"/><path d="M4 7 H9.5 M7.2 4.6 L9.6 7 L7.2 9.4" stroke="#ff8a00" stroke-width="1.6" fill="none"/></svg>
    </a>
  </section>

  <!-- sessions -->
  <section class="sessions">
    <div class="abs session small" style="left:172px;top:743px">
      <svg width="70" height="96" viewBox="0 0 70 96" fill="none" stroke="#fff" stroke-width="3"><circle cx="35" cy="28" r="20"/><path d="M15 30 C12 50 14 60 20 66 M55 30 C58 50 56 60 50 66 M6 96 C6 76 18 66 35 66 C52 66 64 76 64 96 M28 66 V96 M42 66 V96"/></svg>
      Private Session
    </div>
    <div class="abs session big" style="left:425px;top:716px">
      <svg width="116" height="116" viewBox="0 0 116 116" fill="none" stroke="#fff" stroke-width="3"><circle cx="20" cy="14" r="10"/><circle cx="58" cy="14" r="10"/><circle cx="96" cy="14" r="10"/><path d="M4 52 C4 36 10 30 20 30 C30 30 36 36 36 52 M42 52 C42 36 48 30 58 30 C68 30 74 36 74 52 M80 52 C80 36 86 30 96 30 C106 30 112 36 112 52"/><circle cx="39" cy="66" r="10"/><circle cx="77" cy="66" r="10"/><path d="M20 112 C20 92 28 84 39 84 C50 84 58 92 58 112 M58 112 C58 92 66 84 77 84 C88 84 96 92 96 112 M4 112 C4 96 8 90 16 88 M112 112 C112 96 108 90 100 88"/></svg>
      Group Session
    </div>
    <div class="abs session small" style="left:731px;top:743px">
      <svg width="104" height="104" viewBox="0 0 104 104" fill="none" stroke="#fff" stroke-width="3"><circle cx="22" cy="16" r="12"/><circle cx="68" cy="22" r="18"/><circle cx="40" cy="56" r="12"/><circle cx="88" cy="50" r="11"/><circle cx="18" cy="82" r="10"/><circle cx="62" cy="86" r="15"/><path d="M30 24 L36 46 M52 52 L78 48 M32 64 L24 74 M50 64 L56 72 M50 34 L46 45 M28 86 L47 86"/></svg>
      Party
    </div>
    <div class="abs badge" style="left:294px;top:1009px;width:62px;height:62px">1<br>client</div>
    <div class="abs badge big" style="left:570px;top:1032px;width:66px;height:66px">2-5<br>clients</div>
    <div class="abs badge" style="left:855px;top:1009px;width:62px;height:62px">+6<br>clients</div>
  </section>

  <!-- about -->
  <section class="about">
    <div class="abs kicker" style="left:0;top:1184px">About Us</div>
    <h2 class="abs heading" style="left:0;top:1216px">GLOW MUSE</h2>
    <p class="abs">Lorem ipsum dolor sit amet, consectetur adipiscing elit, sed do eiusmod tempor incididunt ut labore et dolore magna aliqua. Quis ipsum suspendisse ultrices gravida. Risus commodo viverra maecenas accumsan lacus vel facilisis. Lorem ipsum dolor sit amet, consectetur adipiscing elit, sed do eiusmod tempor incididunt ut labore et dolore magna aliqua. Quis ipsum suspendisse ultrices gravida. Risus commodo viverra maecenas accumsan lacus vel facilisis.</p>
    <a class="abs btn learn" style="left:509px;top:1407px">LEARN MORE</a>
  </section>

  <!-- products band -->
  <svg class="abs" style="left:0;top:1510px" width="1200" height="832" viewBox="0 0 1200 832" aria-hidden="true">
    <defs><linearGradient id="pinkBand" x1="0" y1="0" x2="1" y2="1"><stop offset="0" stop-color="#e5117d"/><stop offset=".5" stop-color="#ec2b8d"/><stop offset="1" stop-color="#e3117b"/></linearGradient></defs>
    <path d="M0 30 C120 -6 260 0 420 30 C560 56 640 60 780 38 C920 16 1060 8 1200 40 V770 C1080 720 960 730 820 770 C650 820 520 830 380 790 C240 752 110 748 0 772 Z" fill="url(#pinkBand)"/>
  </svg>
  <section class="products">
    <div class="abs kicker" style="left:0;top:1640px">Our Products</div>
    <h2 class="abs heading" style="left:0;top:1672px;font-size:36px">GLOW MUSE PRODUCTS</h2>

    <div class="abs card" style="left:122px;top:1776px">
      <div class="thumb" role="img" aria-label="Photo of a facial skincare treatment" style="background:linear-gradient(140deg,#efe1e4,#d9c3c6)"></div>
      <h3>LOREM IPSUM DOLOR SIT AMET</h3>
      <p>Lorem ipsum dolor sit amet, consectetur adipiscing elit, sed do eiusmod tempor incididunt ut labore</p>
      <a>Learn More</a>
    </div>
    <div class="abs card" style="left:366px;top:1776px">
      <div class="thumb" role="img" aria-label="Photo of a man receiving a relaxing facial" style="background:linear-gradient(140deg,#d9c8bd,#8a6e5e)"></div>
      <h3>LOREM IPSUM DOLOR SIT AMET</h3>
      <p>Lorem ipsum dolor sit amet, consectetur adipiscing elit, sed do eiusmod tempor incididunt ut labore</p>
      <a>Learn More</a>
    </div>
    <div class="abs card" style="left:609px;top:1776px">
      <div class="thumb" role="img" aria-label="Photo of a woman with smooth glowing skin" style="background:linear-gradient(140deg,#f6eeed,#dcc6bd)"></div>
      <h3>LOREM IPSUM DOLOR SIT AMET</h3>
      <p>Lorem ipsum dolor sit amet, consectetur adipiscing elit, sed do eiusmod tempor incididunt ut labore</p>
      <a>Learn More</a>
    </div>
    <div class="abs card" style="left:852px;top:1776px">
      <div class="thumb" role="img" aria-label="Photo of a light therapy skin session" style="background:linear-gradient(140deg,#8fb2c9,#e3d6ce)"></div>
      <h3>LOREM IPSUM DOLOR SIT AMET</h3>
      <p>Lorem ipsum dolor sit amet, consectetur adipiscing elit, sed do eiusmod tempor incididunt ut labore</p>
      <a>Learn More</a>
    </div>

    <div class="abs arrow" style="left:45px;top:1969px;background:#fff"><svg width="10" height="10" viewBox="0 0 10 10"><path d="M6.5 1.5 L3 5 L6.5 8.5" stroke="#e5177f" stroke-width="1.6" fill="none"/></svg></div>
    <div class="abs arrow" style="left:1132px;top:1969px;background:var(--orange)"><svg width="10" height="10" viewBox="0 0 10 10"><path d="M3.5 1.5 L7 5 L3.5 8.5" stroke="#fff" stroke-width="1.6" fill="none"/></svg></div>
  </section>

  <!-- stories -->
  <section class="stories">
    <div class="abs before" role="img" aria-label="Client photo before treatment"></div>
    <div class="abs after" role="img" aria-label="Client photo after treatment"></div>
    <div class="abs tag" style="left:181px;top:2580px;color:var(--pink)">Before</div>
    <div class="abs tag" style="left:422px;top:2665px;color:var(--orange)">After</div>
    <div class="abs" style="left:312px;top:2622px;width:50px;height:50px;border-radius:50%;background:#fff;border:2px solid #f1a4ce"></div>
    <div class="abs kicker" style="left:600px;top:2424px">Our Stories</div>
    <h2 class="abs">Glow Muse Stories</h2>
    <p class="abs">Lorem ipsum dolor sit amet, consectetur adipiscing elit, sed do eiusmod tempor incididunt ut labore et dolore magna aliqua. Quis ipsum suspendisse ultrices gravida. Risus commodo viverra maecenas accumsan lacus vel facilisis. Lorem ipsum dolor sit amet, consectetur adipiscing elit, sed do eiusmod tempor incididunt ut labore et dolore magna aliqua. Quis ipsum suspendisse ultrices gravida. Risus commodo viverra maecenas accumsan lacus vel facilisis. Lorem ipsum dolor sit amet, consectetur adipiscing elit, sed do eiusmod tempor incididunt ut labore et dolore magna aliqua. Quis ipsum suspendisse ultrices gravida. Risus commodo viverra maecenas accumsan lacus vel facilisis.</p>
    <a class="abs btn learn" style="left:599px;top:2809px">LEARN MORE</a>
  </section>

  <!-- footer -->
  <svg class="abs" style="left:0;top:2920px" width="1200" height="572" viewBox="0 0 1200 572" aria-hidden="true">
    <defs><radialGradient id="glow" cx=".45" cy=".5" r=".5"><stop offset="0" stop-color="#1c1c1c"/><stop offset="1" stop-color="#000"/></radialGradient></defs>
    <path d="M0 14 C140 -6 300 30 470 60 C620 84 760 80 920 46 C1040 22 1130 14 1200 22 V572 H0 Z" fill="url(#glow)"/>
  </svg>
  <footer class="footer">
    <div class="abs fbrand"><i></i>Glow Muse</div>
    <h4 class="abs" style="left:127px;top:3162px">Quick Link</h4>
    <ul class="abs" style="left:129px;top:3200px"><li>Home</li><li>About Us</li><li>Stories</li><li>Services</li></ul>
    <h4 class="abs" style="left:332px;top:3162px">Help Link</h4>
    <ul class="abs" style="left:335px;top:3200px"><li>Terms &amp; Conditions</li><li>Privacy Policy</li><li>About Us</li><li>Support</li></ul>
    <h3 class="abs news">Join Our Newsletter</h3>
    <div class="abs email">Enter Your Email</div>
    <a class="abs btn join">Join Now</a>
    <div class="abs contact"><span>+ 155-501-4229</span><span>hello@glowmuse.co</span></div>
    <div class="abs fdots" aria-label="Social links"><span></span><span></span><span></span><span></span></div>
    <div class="abs rule"></div>
    <div class="abs copy">©Copyrights 2022 Glow Muse &nbsp;| &nbsp; All Rights Reserved</div>
  </footer>

</div>
</body>
</html>
```